COVER ONLY - Electrical supply company needs new catalogue cover (front and back)

We're currently finalising our catalogue and have gone through many changes in branding since our last catalogue so need a completely NEW design incorporating the new logo and design feel from the CI document attached.

Since the company is moving more corporate we'd like a much cleaner looking cover (front and back) from what we had before. We'd would like to keep a dominate color for the year so we can simply change the color for the following year catalogue.

We'd like to show product images (supplied) on the front of the catalogue but not as dominate as our previous catalogue (attached to get an idea of where we came from).

We'd like to introduce as much of our new CI into the new catalogue cover as possible while keeping up with our new corporate style of "clean and neat".

I've attached our logo, CI guide, old catalogue cover and some product images.

We would like the file to be handed over in complete format as well as in .psd

(Our website is also being updated but the old website is still up www.qv.co.za)
Updates

Cover size is A4 and the spine will be roughly 3/4 inch.

Please make sure you read the CI guide.

Produce something that shows professionalism, class and style.  We want something that any multi national billion dollar company would be proud to show

Industry/Entity Type

Electrical

Font styles to use
Other font styles liked:
• Sansation

```html
<!DOCTYPE html>
<html lang="en">
<head>
<meta charset="utf-8">
<title>QuadVolt Catalogue Cover</title>
<link rel="stylesheet" href="https://fonts.googleapis.com/css2?family=Open+Sans:ital,wght@0,300;0,400;0,600;0,700;1,700&display=swap">
<style>
  :root {
    --cyan: #1fb3d8;
    --cyan-light: #8fdcef;
    --cyan-bright: #3cc6ea;
    --charcoal: #3a3b3e;
    --charcoal-light: #55575b;
    --grey-text: #6d6e71;
    --ink: #222222;
    --white: #ffffff;
  }
  * { margin: 0; padding: 0; box-sizing: border-box; }
  html, body { width: 1200px; height: 848px; overflow: hidden; background: var(--white); }
  body { font-family: "Open Sans", Arial, sans-serif; }
  .cover { position: relative; width: 1200px; height: 848px; overflow: hidden; }
  .backdrop { position: absolute; inset: 0; }

  .range { position: absolute; left: 41px; top: 100px; width: 520px; color: var(--white); }
  .range h2 { font-size: 16px; font-weight: 700; margin-bottom: 14px; }
  .range h2.section-b { margin-top: 14px; }
  .range p { font-size: 12.6px; line-height: 17px; font-weight: 400; }
  .range .group { margin-bottom: 17px; }
  .range .brands { margin-top: 14px; }

  .contact-title { position: absolute; left: 250px; top: 666px; font-size: 24px; font-weight: 600; color: var(--ink); }
  .contact-rule { position: absolute; left: 65px; top: 710px; width: 432px; height: 1px; background: #c9c9c9; }
  .contact-col { position: absolute; font-size: 12.6px; line-height: 17px; color: var(--ink); font-style: normal; }
  .contact-col.cape { left: 71px; top: 731px; }
  .contact-col.durban { left: 355px; top: 714px; }

  .brand { position: absolute; left: 640px; top: 62px; display: flex; align-items: center; gap: 12px; }
  .brand-square { width: 26px; height: 26px; background: var(--cyan); }
  .brand-name { font-size: 34px; font-weight: 400; color: var(--grey-text); letter-spacing: 0.5px; }

  .tagline { position: absolute; right: 22px; top: 156px; text-align: right; font-size: 30px; line-height: 38px; color: var(--white); font-weight: 300; z-index: 2; }
  .tagline .highlight { color: var(--cyan-bright); font-weight: 700; font-style: italic; }

  .product-range { position: absolute; left: 650px; top: 300px; width: 385px; height: 392px; border-radius: 6px;
    background: radial-gradient(ellipse at 45% 45%, #5c5e62 0%, #45474b 45%, #c9cdd2 80%, rgba(220,225,230,0) 100%); }

  .web { position: absolute; right: 10px; top: 814px; font-size: 15px; font-weight: 700; color: var(--grey-text); }
</style>
</head>
<body>
<main class="cover">
  <svg class="backdrop" width="1200" height="848" viewBox="0 0 1200 848" aria-hidden="true">
    <defs>
      <linearGradient id="back-panel" x1="0" y1="0" x2="1" y2="1">
        <stop offset="0" stop-color="#22b4d9"/>
        <stop offset="0.55" stop-color="#4cc4e4"/>
        <stop offset="1" stop-color="#9fe0f0"/>
      </linearGradient>
      <linearGradient id="front-panel" x1="0" y1="0" x2="1" y2="1">
        <stop offset="0" stop-color="#56585c"/>
        <stop offset="1" stop-color="#2f3033"/>
      </linearGradient>
      <radialGradient id="globe" cx="0.45" cy="0.4" r="0.7">
        <stop offset="0" stop-color="#e7f7fc"/>
        <stop offset="1" stop-color="#8fd8ee"/>
      </radialGradient>
    </defs>
    <rect x="0" y="0" width="601" height="848" fill="url(#back-panel)"/>
    <rect x="601" y="0" width="599" height="145" fill="var(--white)"/>
    <rect x="601" y="145" width="599" height="703" fill="url(#front-panel)"/>
    <circle cx="820" cy="470" r="318" fill="#bfe9f5" opacity="0.55"/>
    <circle cx="820" cy="470" r="300" fill="#ffffff" opacity="0.85"/>
    <circle cx="820" cy="470" r="282" fill="url(#globe)"/>
    <path d="M0 668 C 160 640, 380 650, 601 700 L 601 848 L 0 848 Z" fill="var(--white)"/>
    <path d="M0 655 C 170 625, 400 640, 601 690" fill="none" stroke="#7fd5ec" stroke-width="6"/>
    <path d="M601 812 C 800 800, 1000 760, 1200 690 L 1200 848 L 601 848 Z" fill="var(--white)"/>
    <path d="M601 800 C 820 786, 1010 744, 1200 676" fill="none" stroke="var(--cyan-light)" stroke-width="8"/>
  </svg>

  <section class="range">
    <h2>A : relays</h2>
    <p>PCB, plug-in, step, miniature industrial and power relays; relay interface modules;<br>sockets; daylight switches; solid-state relays and accessories</p>
    <p class="brands">Brands: Relvanta, Solmark</p>
    <h2 class="section-b">B : motor control</h2>
    <div class="group"><p>Control and protection<br>• Contactors • Semi-conductor contactors • Thermal overload relays<br>• Motor control circuit breakers • Motor starters • Soft starters<br>• IC soft starters • Electronic motor protection</p></div>
    <div class="group"><p>Command and signalling<br>• Pushbuttons and selectors • Signal towers and beacons<br>• Limit and foot switches • Rotary cam switches<br>• Joystick controls • Pendant controls • Wormgear limit switches</p></div>
    <div class="group"><p>Switching and circuit protection<br>• Load break switches • Earth leakage relays</p></div>
    <div class="group"><p>Automation and control<br>• Time relays • Protection relays • Level control relays<br>• Programmable logic relays • Switching power supplies</p></div>
    <div class="group"><p>Energy management<br>• Metering instruments (kwh) • Automatic power factor controllers<br>• Automatic battery chargers • Automatic transfer switch controllers<br>• Engine and generator controllers</p></div>
    <p>Brands: Arvelo, Kintor, Protex, NC Controls</p>
  </section>

  <h2 class="contact-title">Contact</h2>
  <div class="contact-rule"></div>
  <address class="contact-col cape">Cape Province<br>14 Harbourview Office Park<br>Marlin Road<br>Riverside Gardens<br>Cape Town</address>
  <address class="contact-col durban">5821&nbsp; P.O. Box 20846<br>Glenmore<br>4061 Durban<br>Telephone: 011 555 0142<br>Telefax: 011 555 0187<br>Email: info@qv.co.za</address>

  <div class="brand">
    <span class="brand-square"></span>
    <span class="brand-name">QuadVolt</span>
  </div>

  <div class="product-range" role="img" aria-label="Product photograph: variable speed drive, moulded case circuit breaker, load break switch, industrial socket and generator controller"></div>

  <h1 class="tagline">Dedicated suppliers of<br><span class="highlight">quality products &amp; service at</span><br>competitive<br>prices</h1>

  <div class="web">www.qv.co.za</div>
</main>
</body>
</html>
```